Stationary Design for Quince consultant and support company

We need new stationary designed for a London based support company that provide on-site and remote support services for Quince products. Our clients are both consumers and businesses.

We would like a letterhead, compliment slip, business card and possibly an e-mail signature designed.

Business card designs can be either 1 side or 2, depending on designs we receive we may choose a preference for 1 or 2 sides later on in the design stage.

Designs needs to be at least 300dpi and should be done using CMYK colours.

We want the design to be bold, easy to read, clean and professional.

We have attached our company logo in 2 colour variations (if you need any other source files then please ask).

Our logo colours are as follows:

Blue (85, 50, 0, 0) and Green (50, 0, 100, 0)

We use two different suppliers for out stationary so here are the size dimensions for both. Unfortunately they are ever so slightly different size wise so hopefully we can get something that accommodates both, we can provide dimensions if required for final versions.

Some fonts that have been used before with our company are Probert (for tagline on our company logo) and previously had Nauman used, however we are very much open to seeing what the designers come up with and the fonts mentioned are not a requirement.
Updates

Company details for designs (however the template should be editable for multiple staff) Lumora Ltd. Registered Office: 62-70 Harrowfield Lane London N7 3QD 020 7591 3384 www.lumora-it.example info@lumora-it.example Company is Registered in England and Wales Company No. 07342519 Directors details (if you want to make the template using his details), rest of the details are as above Dan Frost Director dan@lumora-it.example

Hi all, Thank you for your submissions so far. Could we please ask that you don't use the logo with the tagline from our website for the stationary designs and only the logos provided in the design brief. For the business cards we are looking at normal rectangular business cards to be used and we can provide a template guide for size if needed, please just ask. Regards Lumora Team

Target Market(s)

Our target market are consumers (of all ages) and small/medium businesses.

Industry/Entity Type

Business

Font styles to use
Serif
Sans Serif

Requirements
Must have
• At least business card, letterhead and compliment slip submitted (we need all 3 designed this time round)
Should not have
• Business cards should not have the writing "registered office" (letterheads and compliment slips can along the bottom edge)

```html
<!DOCTYPE html>
<html lang="en">
<head>
<meta charset="utf-8">
<title>Lumora Ltd. — Business Card</title>
<link href="https://fonts.googleapis.com/css2?family=Montserrat:wght@700&family=Questrial&display=swap" rel="stylesheet">
<style>
  :root {
    --backdrop: #3a3a3a;
    --card-white: #f7f7f5;
    --card-dark: #2b2b2b;
    --ink: #3c3c3c;
    --ink-soft: #555555;
    --brand-blue: #2a7fc6;
    --brand-green: #8cc63f;
    --logo-light: #e8e8e8;
  }
  * { box-sizing: border-box; margin: 0; padding: 0; }
  html, body {
    width: 1200px; height: 900px; overflow: hidden;
    background: var(--backdrop);
    font-family: "Questrial", "Century Gothic", sans-serif;
  }
  .canvas {
    position: relative; width: 1200px; height: 900px;
    display: flex; flex-direction: column; align-items: center;
    justify-content: center; gap: 40px;
  }
  .card {
    position: relative; width: 700px; height: 400px; overflow: hidden;
    box-shadow: 0 10px 30px rgba(0,0,0,.35);
  }

  /* Back of card */
  .card-back { background: var(--card-dark); }
  .card-back .wordmark {
    position: absolute; left: 0; right: 0; top: 50%;
    transform: translateY(-50%);
    display: flex; align-items: center; justify-content: center; gap: 16px;
    color: var(--logo-light); font-size: 64px; letter-spacing: 2px;
  }
  .wordmark-square { width: 22px; height: 22px; background: var(--brand-green); }

  /* Front of card */
  .card-front { background: var(--card-white); color: var(--ink); }
  .card-front .wordmark {
    position: absolute; left: 62px; top: 128px;
    color: var(--ink); font-size: 58px; letter-spacing: 2px;
  }
  .person { position: absolute; right: 44px; top: 44px; text-align: right; }
  .person-name {
    font-family: "Montserrat", "Century Gothic", sans-serif;
    font-weight: 700; font-size: 22px; letter-spacing: .5px; color: #2e2e2e;
  }
  .person-role { font-size: 19px; color: var(--ink-soft); margin-top: 2px; }

  .contact-list {
    position: absolute; right: 44px; top: 190px; list-style: none;
    font-size: 15px; color: var(--ink-soft);
  }
  .contact-list li { display: flex; align-items: center; gap: 10px; margin-bottom: 8px; }
  .contact-icon { width: 16px; height: 16px; flex: none; }

  .office {
    position: absolute; left: 62px; bottom: 72px;
    font-size: 15px; line-height: 1.5; color: var(--ink-soft);
  }
  .office-row { display: flex; align-items: center; }
  .office-phone { display: flex; align-items: center; gap: 8px; margin-left: 28px; }
  .card-bands { position: absolute; left: 0; bottom: 0; width: 700px; height: 120px; }
</style>
</head>
<body>
<main class="canvas">

  <section class="card card-back" aria-label="Business card back">
    <div class="wordmark"><span class="wordmark-square"></span>Lumora</div>
  </section>

  <section class="card card-front" aria-label="Business card front">
    <div class="wordmark">Lumora</div>

    <div class="person">
      <div class="person-name">DAN FROST</div>
      <div class="person-role">Director</div>
    </div>

    <ul class="contact-list">
      <li>
        <svg class="contact-icon" viewBox="0 0 16 16" aria-hidden="true">
          <circle cx="8" cy="8" r="7.5" fill="var(--brand-blue)"/>
          <rect x="4" y="5.2" width="8" height="5.6" fill="none" stroke="#fff" stroke-width="1"/>
          <path d="M4 5.2 L8 8.4 L12 5.2" fill="none" stroke="#fff" stroke-width="1"/>
        </svg>
        dan@lumora-it.example
      </li>
      <li>
        <svg class="contact-icon" viewBox="0 0 16 16" aria-hidden="true">
          <circle cx="8" cy="8" r="6.5" fill="none" stroke="var(--brand-blue)" stroke-width="1.3"/>
          <ellipse cx="8" cy="8" rx="2.8" ry="6.5" fill="none" stroke="var(--brand-blue)" stroke-width="1.1"/>
          <path d="M1.5 8 H14.5 M2.6 4.8 H13.4 M2.6 11.2 H13.4" stroke="var(--brand-blue)" stroke-width="1.1"/>
        </svg>
        www.lumora-it.example
      </li>
    </ul>

    <div class="office">
      <div class="office-row">
        <span class="office-street">62-70 Harrowfield Lane</span>
        <span class="office-phone">
          <svg class="contact-icon" viewBox="0 0 16 16" aria-hidden="true">
            <circle cx="8" cy="8" r="7" fill="none" stroke="var(--brand-blue)" stroke-width="1.2"/>
            <path d="M5.4 4.4 L6.8 4.2 L7.4 6 L6.5 6.8 Q7.4 8.8 9.2 9.6 L10 8.7 L11.8 9.3 L11.6 10.7 Q8.6 11.6 6.2 9 Q4.6 7 5.4 4.4 Z" fill="var(--brand-blue)"/>
          </svg>
          020 7591 3384
        </span>
      </div>
      <div class="office-city">London N7 3QD</div>
    </div>

    <svg class="card-bands" viewBox="0 0 700 120" preserveAspectRatio="none" aria-hidden="true">
      <polygon points="0,98 700,36 700,60 0,120" fill="var(--brand-blue)"/>
      <polygon points="560,60 700,18 700,44 540,64" fill="var(--brand-green)"/>
    </svg>
  </section>

</main>
</body>
</html>
```